Business card design for a teacher - double sided, sleek design.

My name is Lina and I am an online Arabic language teacher. I am looking for a beautiful business card design for my online teaching business.

The cards will be printed in 85mm x 55mm size.
The card can be either portrait or landscape.

The design should contain my logo on one side and information on the other.

The design needs to be clean and modern. Use of subtle Arabic geometric patterns would be nice. Icons for the social media information on the card should also match the design theme.

My logo font is Consolas, which is a Monospace font.

Business card design should be delivered with editable PSD or EPS files in the handover.

Thanks

Lina

----

Information on the back:

URL: www.speakwithnadia.net [this should stand out more than other details]
Email: info@speakwithnadia.net
Instagram: @speakwithnadia
Facebook: friendspace.net/speakwithnadia
Skype: speakwithnadia

My brand colours are shown in the logo attached. These are:
- Teal green - 4DC9C1
- Mango yellow - FFD600

Target Market(s)

- Young professionals
- Expatriates
- Women and Men

Industry/Entity Type

Education

Contact Information for Business Card

Information on the back:

Skype: speakwithnadia

- Teal green - 4DC9C1
- Mango yellow - FFD600

Font styles to use
Other font styles liked:
• Any font complimentary to my logo font which is a Monospace font called Consolas.

Colors

Designer to choose colors to be used in the design.

Requirements
Must have
• - Aesthetically pleasing look
• - Complimentary design with existing logo
Nice to have
• Arabic geometrical patterns

```html
<!DOCTYPE html>
<html lang="en">
<head>
<meta charset="utf-8">
<title>Arabic with Lina – Business Card</title>
<link rel="stylesheet" href="https://fonts.googleapis.com/css2?family=Open+Sans:wght@400;600&display=swap">
<style>
  :root {
    --teal: #4dc9c1;
    --teal-soft: #5ccfc7;
    --mango: #ffd600;
    --paper: #f3f3f3;
    --ink: #5f5f5f;
    --rule: #bdbdbd;
    --stage: #2a2a2a;
    --white: #ffffff;
  }
  html, body {
    margin: 0;
    padding: 0;
    width: 1200px;
    height: 960px;
    overflow: hidden;
    background: var(--stage);
  }
  .canvas {
    position: relative;
    width: 1200px;
    height: 960px;
  }
  .card {
    position: absolute;
    width: 600px;
    height: 342px;
    overflow: hidden;
  }
  .card--front { left: 314px; top: 113px; background: var(--paper); }
  .card--back  { left: 311px; top: 472px; background: var(--teal); }

  .card__bands { position: absolute; inset: 0; }

  .brand-name {
    position: absolute;
    left: 44px;
    top: 128px;
    width: 240px;
    margin: 0;
    font-family: "Open Sans", sans-serif;
    font-weight: 400;
    font-size: 32px;
    line-height: 1.1;
    letter-spacing: 1px;
    color: var(--ink);
    text-transform: uppercase;
  }

  .divider {
    position: absolute;
    left: 310px;
    top: 124px;
    width: 1px;
    height: 94px;
    background: var(--rule);
  }
  .contacts {
    position: absolute;
    left: 334px;
    top: 124px;
    margin: 0;
    padding: 0;
    list-style: none;
    font-family: "Open Sans", sans-serif;
    font-size: 13.5px;
    color: var(--ink);
  }
  .contacts li {
    display: flex;
    align-items: center;
    gap: 8px;
    height: 19.3px;
    white-space: nowrap;
  }
  .contacts svg { width: 13px; height: 13px; flex: none; }

  .pattern {
    position: absolute;
    inset: 0;
    background: linear-gradient(135deg, var(--teal-soft), var(--teal));
  }
  .back-name {
    position: absolute;
    left: 0;
    right: 0;
    top: 130px;
    margin: 0;
    text-align: center;
    font-family: "Open Sans", sans-serif;
    font-weight: 400;
    font-size: 30px;
    line-height: 1.2;
    letter-spacing: 3px;
    color: var(--white);
    text-transform: uppercase;
  }
  .back-url {
    position: absolute;
    left: 0;
    right: 0;
    top: 290px;
    margin: 0;
    text-align: center;
    font-family: "Open Sans", sans-serif;
    font-weight: 600;
    font-size: 14px;
    letter-spacing: 6px;
    color: var(--white);
    text-transform: uppercase;
  }
</style>
</head>
<body>
<main class="canvas">

  <section class="card card--front" aria-label="Card front">
    <svg class="card__bands" viewBox="0 0 600 342" aria-hidden="true">
      <polygon points="0,0 575,0 0,53" fill="var(--mango)"/>
      <polygon points="600,290 600,342 25,342" fill="var(--teal)"/>
    </svg>

    <p class="brand-name">Arabic with Lina</p>

    <span class="divider" aria-hidden="true"></span>

    <ul class="contacts">
      <li>
        <svg viewBox="0 0 14 14" aria-hidden="true"><rect x="1" y="3" width="12" height="8" fill="var(--teal)"/><polyline points="1,3 7,8 13,3" fill="none" stroke="var(--paper)" stroke-width="1.2"/></svg>
        info@speakwithnadia.net
      </li>
      <li>
        <svg viewBox="0 0 14 14" aria-hidden="true"><circle cx="7" cy="7" r="6" fill="var(--teal)"/></svg>
        @speakwithnadia
      </li>
      <li>
        <svg viewBox="0 0 14 14" aria-hidden="true"><circle cx="7" cy="7" r="6" fill="var(--teal)"/></svg>
        friendspace.net/speakwithnadia
      </li>
      <li>
        <svg viewBox="0 0 14 14" aria-hidden="true"><circle cx="7" cy="7" r="6" fill="var(--teal)"/></svg>
        speakwithnadia
      </li>
      <li>
        <svg viewBox="0 0 14 14" aria-hidden="true"><circle cx="7" cy="7" r="6" fill="var(--teal)"/><ellipse cx="7" cy="7" rx="2.6" ry="6" fill="none" stroke="var(--paper)" stroke-width="1"/><line x1="1" y1="7" x2="13" y2="7" stroke="var(--paper)" stroke-width="1"/></svg>
        www.speakwithnadia.net
      </li>
    </ul>
  </section>

  <section class="card card--back" aria-label="Card back">
    <div class="pattern" role="img" aria-label="Subtle repeating Arabic geometric tile pattern in soft teal"></div>
    <p class="back-name">Arabic<br>with Lina</p>
    <p class="back-url">www.speakwithnadia.net</p>
  </section>

</main>
</body>
</html>
```